Dusty Spur Outfitters Home Page

I need a logo and page design for my home page, maybe some background color suggestions to go with it. I want the logo to project "vintage" and "western wear" but not be your typical trite western saddle and gun type thing.
http://www.dustyspuroutfitters.example/store/cart.php
Not looking for page coding just logo and other design elements to lay in over the site's template to make it "pop"
Reason: Have to finalize the design.
Target Market(s)
My customers are 70/30 men to women.
Industry/Entity Type
Gun

```html
<!DOCTYPE html>
<html lang="en">
<head>
<meta charset="utf-8">
<title>Dusty Spur Outfitters – Header Concepts</title>
<link rel="stylesheet" href="https://fonts.googleapis.com/css2?family=Lato:wght@700&family=Kaushan+Script&display=swap">
<style>
  :root {
    --canvas-tan: #cdb99b;
    --band-charcoal: #242120;
    --band-red: #4f1d18;
    --band-teal: #3a98a8;
    --band-slate: #2c2c2b;
    --cream: #e7d9bd;
    --logo-cream: #ecd8a6;
    --tagline: #d3c7ad;
    --ink: #2f2c28;
    --go-text: #ddd1bb;
  }
  html, body {
    margin: 0;
    padding: 0;
    width: 1200px;
    height: 1000px;
    overflow: hidden;
  }
  body {
    position: relative;
    background-color: var(--canvas-tan);
    background-image:
      repeating-linear-gradient(45deg, rgba(255,255,255,0.04) 0 2px, rgba(0,0,0,0.03) 2px 4px);
    font-family: "Lato", Arial, sans-serif;
  }
  .header-band {
    position: absolute;
    left: 0;
    width: 1200px;
    height: 167px;
    box-shadow: 0 4px 6px rgba(0,0,0,0.35);
  }
  .header-band--saddle {
    top: 216px;
    background: linear-gradient(to bottom,
      var(--band-charcoal) 0 18px,
      var(--band-red) 18px 148px,
      var(--band-charcoal) 148px 167px);
  }
  .header-band--turquoise {
    top: 566px;
    background: linear-gradient(to bottom,
      var(--band-teal) 0 18px,
      #141414 18px 21px,
      var(--band-slate) 21px 145px,
      #141414 145px 148px,
      var(--band-teal) 148px 167px);
  }
  .brand-mark {
    position: absolute;
    left: 58px;
    top: 8px;
    width: 408px;
    height: 152px;
    display: flex;
    align-items: center;
    justify-content: center;
    gap: 14px;
  }
  .brand-dot {
    width: 18px;
    height: 18px;
    border-radius: 50%;
    background: var(--logo-cream);
    flex: none;
  }
  .brand-name {
    margin: 0;
    color: var(--logo-cream);
    font-family: "Lato", Arial, sans-serif;
    font-weight: 700;
    font-size: 38px;
    line-height: 1.05;
    text-transform: uppercase;
    letter-spacing: 1px;
    text-align: center;
  }
  .tagline {
    position: absolute;
    left: 476px;
    top: 86px;
    margin: 0;
    color: var(--tagline);
    font-family: "Kaushan Script", cursive;
    font-size: 23px;
    white-space: nowrap;
    text-shadow: 1px 2px 2px rgba(0,0,0,0.5);
  }
  .site-search {
    position: absolute;
    left: 901px;
    top: 52px;
    display: flex;
    align-items: center;
    gap: 10px;
  }
  .search-field {
    width: 173px;
    height: 30px;
    box-sizing: border-box;
    padding: 0 17px;
    border-radius: 15px;
    background: var(--cream);
    color: var(--ink);
    font-weight: 700;
    font-size: 18px;
    line-height: 30px;
  }
  .search-go {
    color: var(--go-text);
    font-weight: 700;
    font-size: 18px;
  }
</style>
</head>
<body>
  <header class="header-band header-band--saddle">
    <div class="brand-mark">
      <span class="brand-dot"></span>
      <p class="brand-name">Dusty Spur<br>Outfitters</p>
    </div>
    <p class="tagline">Brand-New Retro Styled Western Wear</p>
    <div class="site-search">
      <div class="search-field">Search...</div>
      <span class="search-go">GO!</span>
    </div>
  </header>

  <header class="header-band header-band--turquoise">
    <div class="brand-mark">
      <span class="brand-dot"></span>
      <p class="brand-name">Dusty Spur<br>Outfitters</p>
    </div>
    <p class="tagline">Brand-New Retro Styled Western Wear</p>
    <div class="site-search">
      <div class="search-field">Search...</div>
      <span class="search-go">GO!</span>
    </div>
  </header>
</body>
</html>
```